Creative Web design for Tattoo Artist

I am a tattoo artist with a private tattoo/art studio in Spring, TX. I need to design a website for my studio, to include the following "pages" :
-home/about
-FAQ
-Gallery
-Inquiries
-shop
We would like to see designs that are more dark or "moody", and like the colors black/gold.
I'd like my website to reflect my studio, an award winning private, upscale custom only tattoo studio.

I've attached some examples of styles we liked.

Target Market(s)

adults ages 18-50, interested in tattoos, or fine art

Industry/Entity Type

Tattoos/Fine Art/Arts

Coding

Coded - Design and coding required

Number of Pages Required

5+ page

Colors

Designer to choose colors to be used in the design.

Requirements
Must have
• gallery section, and e-commerce page set up so I can begin selling merchandise, I'd like the fonts to flow with my logo design

```html
<!DOCTYPE html>
<html lang="en">
<head>
<meta charset="utf-8">
<title>The Gilded Adder — Private Tattoo Studio</title>
<link href="https://fonts.googleapis.com/css2?family=Roboto:wght@400;500&family=Poppins:wght@400;500;600&family=Lora:wght@400&display=swap" rel="stylesheet">
<style>
:root{
  --gold:#b47f31;
  --ink:#0b0b0b;
  --text:#ffffff;
  --muted:#d7d7d7;
  --line:#bdbdbd;
}
*{margin:0;padding:0;box-sizing:border-box}
html,body{width:1200px;height:4383px;overflow:hidden;background:var(--ink)}
body{position:relative;font-family:"Roboto",sans-serif;color:var(--text)}
.abs{position:absolute}
.gold{color:var(--gold)}
.btn{position:absolute;display:flex;align-items:center;justify-content:center;border:2px solid var(--gold);font-family:"Poppins",sans-serif;font-weight:500;font-size:16px;color:#fff;background:transparent}
.btn.white{border-color:#fff}
.photo{position:absolute}

/* hero */
.hero{position:absolute;left:0;top:0;width:1200px;height:600px;overflow:hidden;background:#161616}
.hero-frame{position:absolute;left:0;top:0}
.brand{position:absolute;font-family:"Poppins",sans-serif;font-weight:600;color:var(--gold);font-size:22px;letter-spacing:2px;display:flex;align-items:center;gap:10px;white-space:nowrap}
.brand .dot{width:14px;height:14px;border-radius:50%;background:var(--gold)}
.nav{position:absolute;top:58px;left:0;font-family:"Poppins",sans-serif;font-weight:500;font-size:17px}
.nav span{position:absolute;white-space:nowrap}
.hero-box{position:absolute;left:275px;top:155px;width:650px;height:292px;background:rgba(30,24,16,.6)}
.hero-welcome{position:absolute;top:202px;width:1200px;text-align:center;font-size:24px;font-weight:400}
.hero-title{position:absolute;top:238px;width:1200px;text-align:center;font-size:44px;font-weight:500;line-height:52px}
.hero-sub{position:absolute;top:298px;width:1200px;text-align:center;font-size:19px;font-family:"Poppins",sans-serif}
.follow{position:absolute;left:1128px;top:200px;writing-mode:vertical-rl;font-size:19px;font-weight:500;display:flex;align-items:center;gap:8px}
.follow i{display:block;width:20px;height:20px;border-radius:50%;background:#fff}

/* about */
.about{position:absolute;top:600px;left:0;width:1200px;height:683px;background:radial-gradient(ellipse at 50% 50%,#262626 0%,#161616 70%,#111 100%)}
.label{position:absolute;font-size:15px;text-transform:uppercase;display:flex;align-items:center;gap:10px;white-space:nowrap}
.label::before{content:"";width:72px;height:3px;background:#fff}
.label.plain{text-transform:none}
.h2{position:absolute;font-size:31px;line-height:36px;font-weight:500;white-space:nowrap}
.about p{position:absolute;left:632px;top:235px;width:470px;font-family:"Lora",serif;font-size:14.5px;line-height:31px;color:var(--muted)}

/* shop */
.shop{position:absolute;top:1283px;left:0;width:1200px;height:692px;background:linear-gradient(#0d0d0d,#111 60%,#161616)}
.product{position:absolute;width:280px;text-align:center}
.product .ring{width:270px;height:270px;margin:0 auto;border-radius:50%;border:10px solid #3a3228;background:#2a2a2a;padding:8px}
.product .art{width:100%;height:100%;border-radius:50%}
.product h3{font-size:26px;font-weight:500;margin-top:26px}
.product .price{color:var(--gold);font-size:20px;margin-top:8px}

/* gallery */
.gallery{position:absolute;top:1975px;left:0;width:1200px;height:865px;background:#161616}

/* faq */
.faq{position:absolute;top:2840px;left:0;width:1200px;height:825px;background:linear-gradient(#101010,#161616)}
.faq-item{position:absolute;left:230px;width:740px;border:1px solid var(--line);border-radius:6px;font-size:16px}
.faq-item.open{border-color:var(--gold);background:#2a2217}
.faq-item .q{position:absolute;left:28px;top:24px}
.faq-item .sign{position:absolute;right:30px;top:16px;font-size:30px;font-weight:300;color:var(--gold)}
.faq-item .a{position:absolute;left:28px;top:72px;width:690px;font-size:16px;line-height:30px;color:var(--muted)}

/* footer */
.footer{position:absolute;top:3665px;left:0;width:1200px;height:718px;background:#0c0c0c;border:2px solid var(--gold);border-bottom:none}
.field{position:absolute;height:55px;border:1.5px solid #8a8a8a;border-radius:4px;font-size:15px;padding:17px 18px;color:#ddd}
.col h4{position:absolute;font-size:20px;font-weight:500}
.col li{position:absolute;list-style:none;font-size:15px;white-space:nowrap;display:flex;align-items:center;gap:8px}
.col li::before{content:"«";color:var(--gold);font-size:18px;line-height:1}
.social{position:absolute;top:4315px;width:22px;height:22px;border-radius:50%;background:var(--gold)}
</style>
</head>
<body>

<!-- HERO -->
<section class="hero">
  <div class="photo" role="img" aria-label="Monochrome photo of a tattoo artist working on a tattooed client's arm in a dark studio" style="left:0;top:0;width:1200px;height:600px;background:linear-gradient(100deg,#2a2a2a 0%,#3c3c3c 30%,#2b2b2b 55%,#4a4a4a 75%,#1e1e1e 100%)"></div>
  <svg class="hero-frame" width="1200" height="600" viewBox="0 0 1200 600">
    <path d="M18 14 H1180 V505 Q1180 585 1100 585 H18 Z" fill="none" stroke="#b47f31" stroke-width="2.5"/>
    <g stroke="#fff" stroke-width="2" fill="none">
      <path d="M102 528 h24 M102 528 l6 -4 M102 528 l6 4"/>
      <path d="M140 528 h24 M164 528 l-6 -4 M164 528 l-6 4"/>
    </g>
    <text x="128" y="534" fill="#fff" font-size="16" font-family="Roboto,sans-serif">1</text>
  </svg>
  <div class="brand" style="left:92px;top:112px"><span class="dot"></span>GILDED ADDER</div>
  <nav class="nav">
    <span class="gold" style="left:404px">Home</span>
    <span style="left:494px">FAQ</span>
    <span style="left:566px">Gallery</span>
    <span style="left:665px">Inquiries</span>
    <span style="left:778px">Shop</span>
  </nav>
  <svg class="abs" style="left:850px;top:58px" width="80" height="30" viewBox="0 0 80 30">
    <circle cx="12" cy="13" r="8" fill="none" stroke="#fff" stroke-width="3"/>
    <path d="M18 19 l7 7" stroke="#fff" stroke-width="3"/>
    <path d="M46 8 h4 l4 13 h14 l3 -9 h-19" fill="none" stroke="#fff" stroke-width="2.5"/>
    <circle cx="57" cy="26" r="2" fill="#fff"/><circle cx="66" cy="26" r="2" fill="#fff"/>
    <text x="72" y="10" fill="#fff" font-size="12" font-family="Roboto,sans-serif">0</text>
  </svg>
  <div class="btn" style="left:958px;top:47px;width:142px;height:51px">Contact Us</div>
  <div class="hero-box"></div>
  <div class="hero-welcome">Welcome To</div>
  <h1 class="hero-title">THE <span class="gold">GILDED</span> ADDER</h1>
  <div class="hero-sub">My body is my journal, and my tattoos are my story.</div>
  <div class="btn white" style="left:452px;top:345px;width:141px;height:50px">Contact Us</div>
  <div class="btn" style="left:607px;top:345px;width:140px;height:50px">Learn More</div>
  <div class="follow">Follow Us : <i></i><i></i><i></i></div>
</section>

<!-- ABOUT -->
<section class="about">
  <div class="photo" role="img" aria-label="Black and white photo of a gloved hand tattooing an arm" style="left:99px;top:111px;width:468px;height:468px;border-radius:50%;background:linear-gradient(135deg,#555 0%,#3a3a3a 50%,#2a2a2a 100%)"></div>
  <svg class="abs" style="left:90px;top:100px" width="510" height="500" viewBox="0 0 510 500">
    <path d="M260 8 A240 240 0 0 1 150 478" fill="none" stroke="#b47f31" stroke-width="6"/>
  </svg>
  <div class="label" style="left:632px;top:123px">About The Gilded Adder</div>
  <h2 class="h2" style="left:632px;top:155px">Tattoo Art has been<br>Offering <span class="gold">Top Quality</span> Work..</h2>
  <p>It is a long established fact that a reader will be distracted by the readable content of a page when looking at its layout. The point of using Lorem Ipsum is that it has a more-or-less normal distribution of letters, as opposed to using 'Content here, content here', making it look like readable English. Many desktop publishing packages and web page editors now use Lorem Ipsum as their default model text, and a search for 'lorem ipsum' will uncover many web sites still in their infancy.</p>
  <div class="btn" style="left:630px;top:503px;width:142px;height:50px">Learn More</div>
</section>

<!-- SHOP -->
<section class="shop">
  <div class="label" style="left:432px;top:80px">Shop The Gilded Adder</div>
  <h2 class="h2" style="left:0;width:1200px;text-align:center;top:112px">Tattoo Art has been <span class="gold">Offering Top</span> Quality Work..</h2>
  <svg class="abs" style="left:48px;top:322px" width="1120" height="36" viewBox="0 0 1120 36">
    <path d="M16 4 l-12 14 l12 14" fill="none" stroke="#fff" stroke-width="2"/>
    <path d="M1096 4 l12 14 l-12 14" fill="none" stroke="#fff" stroke-width="2"/>
  </svg>
  <div class="product" style="left:95px;top:192px">
    <div class="ring"><div class="art" role="img" aria-label="Black tribal wolf tattoo design on a light ground" style="background:radial-gradient(circle,#6a6a6a 0%,#9a9896 40%,#dcdad7 75%)"></div></div>
    <h3>Tribal Wolf</h3><div class="price">$98.00</div>
  </div>
  <div class="product" style="left:460px;top:192px">
    <div class="ring"><div class="art" role="img" aria-label="Grey shaded roses bouquet tattoo design" style="background:radial-gradient(circle,#8a8a8a 0%,#b4b2af 45%,#dcdad7 80%)"></div></div>
    <h3>Roses Bouquet</h3><div class="price">$98.00</div>
  </div>
  <div class="product" style="left:823px;top:192px">
    <div class="ring"><div class="art" role="img" aria-label="Crescent moon with hanging flowers line tattoo design" style="background:radial-gradient(circle at 40% 50%,#a9a7a4 0%,#c8c6c3 45%,#dedcd9 80%)"></div></div>
    <h3>Moon Flower</h3><div class="price">$98.00</div>
  </div>
  <div class="btn" style="left:165px;top:560px;width:142px;height:50px">View More</div>
  <div class="btn" style="left:529px;top:560px;width:142px;height:50px">View More</div>
  <div class="btn" style="left:893px;top:560px;width:142px;height:50px">View More</div>
</section>

<!-- GALLERY -->
<section class="gallery">
  <div class="label" style="left:506px;top:67px">Our Gallery</div>
  <h2 class="h2" style="left:0;width:1200px;text-align:center;top:96px">Upscale <span class="gold">Custom-only</span> Tattoo Studio</h2>
  <div class="photo" role="img" aria-label="Black-gloved hands holding a tattoo machine" style="left:97px;top:182px;width:323px;height:291px;background:linear-gradient(135deg,#2e3236,#1a1a1a 55%,#4a3a30)"></div>
  <div class="photo" role="img" aria-label="Forearm with a fresh botanical line tattoo" style="left:432px;top:182px;width:668px;height:291px;background:linear-gradient(90deg,#1e1a18,#5a3e30 45%,#8a5e46 75%,#3a2a22)"></div>
  <div class="photo" role="img" aria-label="Portrait of a man with a colourful chest tattoo" style="left:97px;top:485px;width:323px;height:292px;background:linear-gradient(#3e4044,#6a4a3a 55%,#7a5a40 80%,#2a221c)"></div>
  <div class="photo" role="img" aria-label="Black and white close-up of a tattoo being applied" style="left:432px;top:485px;width:668px;height:292px;border:5px solid var(--gold);border-radius:0 60px 0 60px;background:linear-gradient(120deg,#3c3c3c,#5a5a5a 55%,#8a8a8a)"></div>
  <svg class="abs" style="left:750px;top:616px" width="30" height="30" viewBox="0 0 30 30">
    <circle cx="12" cy="12" r="8" fill="none" stroke="#fff" stroke-width="3"/><path d="M18 18 l8 8" stroke="#fff" stroke-width="3.5"/>
  </svg>
</section>

<!-- FAQ -->
<section class="faq">
  <div class="label plain" style="left:458px;top:82px">Award-Winning Private</div>
  <h2 class="h2" style="left:0;width:1200px;text-align:center;top:122px">Frequently <span class="gold">Asked</span> Questions</h2>
  <div class="faq-item" style="top:190px;height:72px"><span class="q">1. Sed ut perspiciatis unde omnis iste natus error sit voluptatem</span><span class="sign">+</span></div>
  <div class="faq-item open" style="top:283px;height:182px"><span class="q">2. Where can I get some?</span><span class="sign">—</span>
    <span class="a">Lorem ipsum dolor sit amet, consectetur adipiscing elit, sed do eiusmod tempor incididunt ut labore et dolore magna aliqua. Ut enim ad minim veniam, quis nostrud exercitation ullamco laboris nisi ut aliquip ex ea commodo consequat.</span></div>
  <div class="faq-item" style="top:492px;height:71px"><span class="q">3. What is Lorem Ipsum?</span><span class="sign">+</span></div>
  <div class="faq-item" style="top:591px;height:71px"><span class="q">4. Where does it come from?</span><span class="sign">+</span></div>
</section>

<!-- FOOTER -->
<footer class="footer">
  <div class="brand" style="left:95px;top:155px;font-size:20px"><span class="dot"></span>GILDED ADDER</div>
  <h2 class="abs" style="left:343px;top:96px;font-size:30px;font-weight:400">Join Our Newsletter</h2>
  <div class="field" style="left:341px;top:157px;width:320px">Enter Name</div>
  <div class="field" style="left:683px;top:157px;width:322px">Enter Email</div>
  <div class="btn" style="left:341px;top:235px;width:320px;height:55px;font-family:Roboto,sans-serif;font-size:18px">SUBMIT NOW</div>
  <div class="col">
    <h4 style="left:98px;top:355px">Quick Links</h4>
    <li style="left:96px;top:395px">Home</li><li style="left:96px;top:425px">FAQ</li><li style="left:96px;top:455px">Gallery</li><li style="left:96px;top:486px">Inquiries</li><li style="left:96px;top:517px">shop</li>
    <h4 style="left:318px;top:355px">Support</h4>
    <li style="left:316px;top:395px">Help Center &amp; FAQs</li><li style="left:316px;top:425px">Contact Us</li><li style="left:316px;top:455px">Developer API Docs</li><li style="left:316px;top:486px">Employer Resources</li><li style="left:316px;top:517px">Account Login</li>
    <h4 style="left:597px;top:355px">LEGAL</h4>
    <li style="left:595px;top:395px">Terms of Service</li><li style="left:595px;top:425px">Privacy Policy</li><li style="left:595px;top:455px">FCRA Obligations</li>
    <h4 style="left:813px;top:355px">LEGAL</h4>
    <li style="left:811px;top:395px;font-size:16px">CALL: +1 555 010 0199</li><li style="left:811px;top:430px;font-size:16px">MAIL: info@thegildedadder.example</li>
  </div>
  <div class="abs" style="left:96px;top:630px;width:1006px;height:1px;background:#777"></div>
  <div class="abs" style="left:96px;top:650px;font-size:16px">Copyrights@2022.<span class="gold">THE GILDEDADDER</span>.All Rights Reserved</div>
</footer>
<div class="social" style="left:1018px"></div>
<div class="social" style="left:1049px"></div>
<div class="social" style="left:1080px"></div>

</body>
</html>
```